Business Cards for Branding (Advertising) Agency

We need stylish and cool business cards.
Additional info:
1) Logo - see the attachment. You can use either the three penguins or just one penguin face (square or round) - at your discretion.
2) Text and other stuff for business card:
front side:
-Logo and company name: company name - Northern Walruses - should be in English as is in logo. This is the only exception. The rest of the text will be in Russian.
-Who we are: Брендинговое агентство
-First and last name:
-Position: Управляющий партнёр
-Address:
-Phone:
-Email:
-Website:
Note: please don't use names of information fields, such as: who we are, first and last name, position, address, phone, email and website.

3) Our suggestions on design:
-The backside of the business card can be either blank or has something on it - at your discretion.
-The business card background should be either white or grey (you can use any tone of grey).

Additional Information:
1) БРЕНДИНГОВОЕ АГЕНТСТВО
2) ул. Кедровская - these two words should be together on the same line
3) тел.: +7 (495) 381-96-02
моб.: +7 (916) 507-28-94

```html
<!DOCTYPE html>
<html lang="ru">
<head>
<meta charset="utf-8">
<title>Northern Walruses — визитные карточки</title>
<link href="https://fonts.googleapis.com/css2?family=Roboto:wght@300;400;700&display=swap" rel="stylesheet">
<style>
  :root {
    --bg: #e4e1dc;
    --card: #ffffff;
    --orange: #f29d12;
    --ink: #1b1b1b;
    --grey: #8a8a8a;
    --white: #ffffff;
  }
  * { box-sizing: border-box; margin: 0; padding: 0; }
  html, body { width: 1200px; height: 1000px; overflow: hidden; }
  body {
    background: var(--bg);
    font-family: "Roboto", Arial, sans-serif;
    position: relative;
  }
  .card {
    position: absolute;
    width: 560px;
    height: 320px;
    background: var(--card);
    border-radius: 18px;
    box-shadow: 0 6px 18px rgba(0,0,0,0.12);
    overflow: hidden;
  }
  .card--front { left: 90px; top: 110px; }
  .card--back { left: 550px; top: 560px; }

  .front-logo {
    position: absolute;
    inset: 0;
    display: flex;
    flex-direction: column;
    align-items: center;
    justify-content: center;
    gap: 14px;
  }
  .front-logo__row { display: flex; align-items: center; gap: 16px; }
  .front-logo__dot {
    width: 28px; height: 28px;
    border-radius: 50%;
    background: var(--ink);
  }
  .front-logo__name {
    font-weight: 400;
    font-size: 34px;
    letter-spacing: 3px;
    color: var(--ink);
    text-transform: uppercase;
  }
  .tagline {
    font-size: 14px;
    font-weight: 400;
    letter-spacing: 4px;
    color: var(--grey);
    text-transform: uppercase;
  }

  .band {
    position: absolute;
    left: 0; top: 0;
    width: 560px; height: 320px;
  }
  .band polygon { fill: var(--orange); }
  .band-brand {
    position: absolute;
    right: 24px;
    top: 56px;
    font-size: 15px;
    font-weight: 700;
    letter-spacing: 1.5px;
    color: var(--white);
    text-transform: uppercase;
  }
  .person {
    position: absolute;
    left: 34px;
    top: 104px;
    color: var(--white);
  }
  .person__name { font-weight: 700; font-size: 19px; line-height: 1.2; }
  .person__role { font-weight: 300; font-size: 16px; margin-top: 2px; }

  .contacts {
    position: absolute;
    left: 34px;
    top: 196px;
    list-style: none;
    color: var(--grey);
    font-size: 16px;
    font-weight: 300;
  }
  .contacts li {
    display: flex;
    align-items: center;
    gap: 12px;
    height: 22px;
  }
  .contacts svg { width: 14px; height: 14px; fill: var(--orange); flex: none; }
  .address {
    position: absolute;
    left: 34px;
    top: 287px;
    font-size: 17px;
    font-weight: 400;
    color: var(--ink);
  }
</style>
</head>
<body>

  <section class="card card--front" aria-label="Лицевая сторона">
    <div class="front-logo">
      <div class="front-logo__row">
        <span class="front-logo__dot"></span>
        <span class="front-logo__name">Northern Walruses</span>
      </div>
      <p class="tagline">Брендинговое агентство</p>
    </div>
  </section>

  <section class="card card--back" aria-label="Оборотная сторона">
    <svg class="band" viewBox="0 0 560 320" aria-hidden="true">
      <polygon points="0,95 560,20 560,105 0,190"/>
    </svg>
    <span class="band-brand">Northern Walruses</span>
    <div class="person">
      <p class="person__name">Мария Ветрова</p>
      <p class="person__role">Управляющий партнёр</p>
    </div>

    <ul class="contacts">
      <li>
        <svg viewBox="0 0 24 24" aria-hidden="true"><path d="M6.6 10.8a15.1 15.1 0 0 0 6.6 6.6l2.2-2.2a1 1 0 0 1 1-.25 11.4 11.4 0 0 0 3.6.57 1 1 0 0 1 1 1V20a1 1 0 0 1-1 1A17 17 0 0 1 3 4a1 1 0 0 1 1-1h3.5a1 1 0 0 1 1 1c0 1.25.2 2.45.57 3.57a1 1 0 0 1-.25 1z"/></svg>
        тел.: +7 (495) 381-96-02
      </li>
      <li>
        <svg viewBox="0 0 24 24" aria-hidden="true"><path d="M6.6 10.8a15.1 15.1 0 0 0 6.6 6.6l2.2-2.2a1 1 0 0 1 1-.25 11.4 11.4 0 0 0 3.6.57 1 1 0 0 1 1 1V20a1 1 0 0 1-1 1A17 17 0 0 1 3 4a1 1 0 0 1 1-1h3.5a1 1 0 0 1 1 1c0 1.25.2 2.45.57 3.57a1 1 0 0 1-.25 1z"/></svg>
        моб.: +7 (916) 507-28-94
      </li>
      <li>
        <svg viewBox="0 0 24 24" aria-hidden="true"><path d="M2 5h20v14H2z M2 5l10 8 10-8"/></svg>
        maria@northwalrus.ru
      </li>
      <li>
        <svg viewBox="0 0 24 24" aria-hidden="true"><circle cx="5" cy="19" r="2.5"/><path d="M3 10a11 11 0 0 1 11 11h-3a8 8 0 0 0-8-8z"/><path d="M3 3a18 18 0 0 1 18 18h-3A15 15 0 0 0 3 6z"/></svg>
        www.northwalrus.ru
      </li>
    </ul>

    <p class="address">117342, г. Москва, ул. Кедровская, д.12, стр.2</p>
  </section>

</body>
</html>
```